Fenwick Grading LTD - website for irrigation & Landscape Lighting & Buried service wire

Looking for a website to help promote my business with Irrigation (installation, service, etc) and buried service wire/drainage solutions.

Commercial/Residential

Landscape lighting.

I’ll get photos in the trucks and trailers to upload as well maybe the machine as well.

Target Market(s)

Homeowners who want green grass and beautiful gardens. Beautiful landscape lighting

Industry/Entity Type

Irrigation systems and landscape lighting and buried service wire to homes and offering Drainage soltions.

Coding

Coded - Design and coding required

Number of Pages Required

4 page

Colors
F0912C
F2A743
F7CA91
FBE8D2
FDF5EE

Requirements
Must have
• was hoping to link up my email on fenwickgrading@mailbox-example.net with the website if possible.
Nice to have
• Page for Irrigation, page for landscape lighting, page buried service wire & drainage soltions.

```html
<!DOCTYPE html>
<html lang="en">
<head>
<meta charset="utf-8">
<title>Fenwick Grading LTD</title>
<link href="https://fonts.googleapis.com/css2?family=Michroma&family=Roboto:wght@400;500;700&display=swap" rel="stylesheet">
<style>
:root{
  --orange:#F0912C;
  --orange-2:#F2A743;
  --orange-3:#F7CA91;
  --orange-4:#FBE8D2;
  --cream:#FDF5EE;
  --ink:#333333;
  --grey:#666666;
  --btn-grey:#7a7a7a;
  --footer:#2b2b2b;
  --white:#ffffff;
}
*{box-sizing:border-box;margin:0;padding:0}
html,body{width:1200px;height:3905px;overflow:hidden}
body{position:relative;background:var(--white);font-family:'Roboto',sans-serif;color:var(--ink)}
.abs{position:absolute}
.display{font-family:'Michroma',sans-serif;font-weight:400;text-transform:uppercase}
.accent{color:var(--orange)}
.photo{position:absolute}

/* header */
.header{left:0;top:0;width:1200px;height:136px;background:var(--white)}
.logo-box{left:103px;top:0;width:221px;height:179px;background:var(--white);border:7px solid var(--orange);border-top:none;z-index:3;display:flex;flex-direction:column;align-items:center;justify-content:center;gap:8px}
.logo-mark{width:22px;height:22px;background:var(--orange)}
.logo-name{font-family:'Roboto',sans-serif;font-weight:700;font-size:21px;color:var(--orange);text-align:center;line-height:1.15;text-transform:uppercase}
.header-phone{left:700px;top:34px;display:flex;align-items:center;gap:12px;font-size:17px;font-weight:500;color:var(--ink)}
.btn-contact{left:956px;top:26px;width:132px;height:47px;background:var(--orange);color:var(--white);font-weight:700;font-size:14px;display:flex;align-items:center;justify-content:center}
.nav{top:99px;font-size:12.5px;font-weight:700;color:var(--ink);text-transform:uppercase;white-space:nowrap}
.nav.active{color:var(--orange)}

/* hero */
.hero{left:0;top:136px;width:1200px;height:643px;background:linear-gradient(180deg,#3a3f22 0%,#4f5a24 45%,#3c4a1a 75%,#2a3312 100%)}
.hero-title{left:220px;top:336px;width:760px;text-align:center;color:var(--white);font-size:25px;line-height:36px;letter-spacing:-0.5px}
.hero-sub{left:150px;top:456px;width:900px;text-align:center;color:var(--white);font-size:18px}
.btn-hero{left:530px;top:505px;width:140px;height:45px;background:var(--white);color:var(--ink);font-size:14px;font-weight:500;display:flex;align-items:center;justify-content:center}
.call-block{left:688px;top:629px;width:418px;height:625px;background:var(--orange)}
.call-text{left:812px;top:652px;color:var(--white)}
.call-text small{display:block;font-size:11px;margin-bottom:6px}
.call-text strong{font-family:'Michroma',sans-serif;font-weight:400;font-size:20px}

/* about */
.about-card{left:111px;top:723px;width:977px;height:513px;background:var(--white);box-shadow:0 6px 20px rgba(0,0,0,.08)}
.about-title{left:653px;top:808px;font-size:33px;color:#555}
.about-text{left:653px;top:866px;width:392px;font-size:14.5px;line-height:25px;color:var(--grey);text-align:justify}
.about-text p+p{margin-top:9px}
.btn-grey{left:653px;top:1101px;width:133px;height:46px;background:var(--btn-grey);color:var(--white);font-size:14px;font-weight:500;display:flex;align-items:center;justify-content:center}

/* services */
.section-title{left:0;width:1200px;text-align:center;font-size:38px;color:#555}
.service-frame{top:1452px;width:297px;height:333px;border:1.5px solid #bbb}
.arrow-box{width:76px;height:74px;background:var(--white);display:flex;align-items:center;justify-content:center}
.service-title{top:1817px;font-size:18.5px;font-weight:500;color:#444;text-transform:uppercase;white-space:nowrap}
.service-text{top:1852px;width:300px;font-size:14.5px;line-height:25px;color:var(--grey)}

/* portfolio */
.portfolio{left:0;top:2012px;width:1200px;height:741px;background:var(--orange)}
.tile{border:3px solid var(--white)}

/* testimonials */
.t-card{top:2997px;width:306px;height:321px;background:var(--white);border-top:5px solid var(--orange);border-radius:8px;box-shadow:0 4px 18px rgba(0,0,0,.1);text-align:center}
.avatar{width:92px;height:92px;border-radius:50%;border:4px solid var(--orange);background:radial-gradient(circle,#d9c9b8,#9c8a78)}
.t-name{font-size:15px;font-weight:500;color:#444;margin-top:75px;text-transform:uppercase}
.t-stars{color:var(--orange);font-size:12px;letter-spacing:2px;margin-top:6px}
.t-text{font-size:14.5px;line-height:26px;color:var(--grey);padding:0 25px;margin-top:10px}
.slide-btn{top:3139px;width:34px;height:34px;border-radius:50%;display:flex;align-items:center;justify-content:center}

/* footer */
.footer{left:0;top:3441px;width:1200px;height:464px;background:var(--footer);color:var(--white)}
.f-title{top:78px;font-size:17px;font-weight:700;text-transform:uppercase}
.f-nav{left:111px;top:124px;list-style:none}
.f-nav li{font-size:13px;font-weight:700;height:34.3px;text-transform:uppercase;display:flex;gap:22px;white-space:nowrap}
.f-nav li::before{content:"»";color:var(--orange)}
.f-contact{left:371px;display:flex;gap:22px}
.f-icon{width:35px;height:35px;background:var(--orange);display:flex;align-items:center;justify-content:center;flex-shrink:0}
.f-contact b{display:block;font-size:14px;margin-bottom:8px}
.f-contact span{font-size:11.5px;line-height:20px}
.field{border:1px solid #777;font-size:14px;padding:14px 16px;color:#ddd}
.btn-send{left:627px;top:327px;width:159px;height:48px;background:var(--orange);font-size:14px;font-weight:700;display:flex;align-items:center;justify-content:center}
.f-rule{left:111px;top:398px;width:977px;height:1px;background:#555}
.copyright{left:0;top:421px;width:1200px;text-align:center;font-size:12px}
.social{top:405px;width:36px;height:36px;border-radius:50%;display:flex;align-items:center;justify-content:center}
</style>
</head>
<body>

<!-- header -->
<div class="abs header"></div>
<div class="abs logo-box"><div class="logo-mark"></div><div class="logo-name">Fenwick Grading<br>LTD</div></div>
<div class="abs header-phone">
  <svg width="26" height="26" viewBox="0 0 24 24"><path d="M6.6 10.8a15 15 0 0 0 6.6 6.6l2.2-2.2c.3-.3.7-.4 1-.2 1.1.4 2.3.6 3.6.6.6 0 1 .4 1 1V20c0 .6-.4 1-1 1A17 17 0 0 1 3 4c0-.6.4-1 1-1h3.5c.6 0 1 .4 1 1 0 1.3.2 2.5.6 3.6.1.3 0 .7-.2 1z" fill="#F0912C"/></svg>
  +1 (888) 888 8888
</div>
<div class="abs btn-contact">CONTACT US</div>
<div class="abs nav active" style="left:386px">Home</div>
<div class="abs nav" style="left:447px">About Us</div>
<div class="abs nav" style="left:530px">Irrigation Installs</div>
<div class="abs nav" style="left:685px">Services</div>
<div class="abs nav" style="left:767px">Landscape Lighting</div>
<div class="abs nav" style="left:925px">Buried Wire &amp; Drainage</div>

<!-- hero -->
<div class="abs hero" role="img" aria-label="Evening garden lawn with glowing landscape path lights"></div>
<h1 class="abs hero-title display">Homeowners who want green grass and beautiful gardens. Beautiful landscape lighting</h1>
<p class="abs hero-sub">Irrigation systems, landscape lighting and buried service wire to homes</p>
<div class="abs btn-hero">GET STARTED</div>
<div class="abs call-block"></div>
<svg class="abs" style="left:752px;top:652px" width="42" height="44" viewBox="0 0 24 24"><path d="M6.6 10.8a15 15 0 0 0 6.6 6.6l2.2-2.2c.3-.3.7-.4 1-.2 1.1.4 2.3.6 3.6.6.6 0 1 .4 1 1V20c0 .6-.4 1-1 1A17 17 0 0 1 3 4c0-.6.4-1 1-1h3.5c.6 0 1 .4 1 1 0 1.3.2 2.5.6 3.6.1.3 0 .7-.2 1z" fill="#fff"/><path d="M14 3a7 7 0 0 1 7 7M14 6.5a3.5 3.5 0 0 1 3.5 3.5" stroke="#fff" stroke-width="1.6" fill="none"/></svg>
<div class="abs call-text"><small class="display">Call us today:</small><strong>+1 (888) 888 8888</strong></div>

<!-- about -->
<div class="abs about-card"></div>
<div class="photo" style="left:153px;top:765px;width:429px;height:427px;background:linear-gradient(135deg,#8a8680 0%,#4a4c5c 45%,#c46a35 80%,#9c958c 100%)" role="img" aria-label="Technician kneeling beside a wall laying orange service wire"></div>
<h2 class="abs about-title display"><span class="accent">About</span> Us</h2>
<div class="abs about-text">
  <p>Lorem ipsum dolor sit amet, consectetur adipiscing elit, sed do eiusmod tempor incididunt ut labore et dolore magna aliqua. Ut enim ad minim veniam, quis nostrud exercitation ullamco laboris nisi ut aliquip ex com modo consequat duis autea.</p>
  <p>Lorem ipsum dolor sit amet, consectetur adipiscing elit, sed do eiusmod tempor incididunt ut labore et dolore magna aliqua ut enim ad minimea.</p>
</div>
<div class="abs btn-grey">LEARN MORE</div>

<!-- services -->
<h2 class="abs section-title display" style="top:1355px"><span class="accent">Our</span> Services</h2>

<div class="abs service-frame" style="left:111px"></div>
<div class="photo" style="left:120px;top:1444px;width:297px;height:333px;background:linear-gradient(135deg,#5c7a2c,#e08a3a 55%,#6e8f33)" role="img" aria-label="Hands adjusting an orange sprinkler head on grass"></div>
<div class="abs arrow-box" style="left:341px;top:1703px"><svg width="46" height="24" viewBox="0 0 46 24"><path d="M2 12h40M31 2l11 10-11 10" stroke="#F0912C" stroke-width="3" fill="none"/></svg></div>
<h3 class="abs service-title" style="left:111px">Irrigation Installs</h3>
<p class="abs service-text" style="left:111px">Lorem ipsum dolor sit amet, consectetu adipiscing elit, sed do eiusmod tempor incididunt ut laborea.</p>

<div class="abs service-frame" style="left:447px"></div>
<div class="photo" style="left:456px;top:1444px;width:297px;height:333px;background:linear-gradient(160deg,#4d4a2e,#2f3b2a 45%,#4a4a6a 80%)" role="img" aria-label="Garden rocks lit by round landscape lights at dusk"></div>
<div class="abs arrow-box" style="left:677px;top:1703px"><svg width="46" height="24" viewBox="0 0 46 24"><path d="M2 12h40M31 2l11 10-11 10" stroke="#F0912C" stroke-width="3" fill="none"/></svg></div>
<h3 class="abs service-title" style="left:447px">Landscape Lighting</h3>
<p class="abs service-text" style="left:447px">Lorem ipsum dolor sit amet, consectetu adipiscing elit, sed do eiusmod tempor incididunt ut laborea.</p>

<div class="abs service-frame" style="left:783px"></div>
<div class="photo" style="left:792px;top:1444px;width:297px;height:333px;background:linear-gradient(135deg,#c9b89a,#8a6a48 45%,#3a3226 85%)" role="img" aria-label="Open trench with buried service wire and drainage pipe"></div>
<div class="abs arrow-box" style="left:1013px;top:1703px"><svg width="46" height="24" viewBox="0 0 46 24"><path d="M2 12h40M31 2l11 10-11 10" stroke="#F0912C" stroke-width="3" fill="none"/></svg></div>
<h3 class="abs service-title" style="left:783px">Buried Wire &amp; Drainage</h3>
<p class="abs service-text" style="left:783px">Lorem ipsum dolor sit amet, consectetu adipiscing elit, sed do eiusmod tempor incididunt ut laborea.</p>

<!-- portfolio -->
<div class="abs portfolio"></div>
<h2 class="abs section-title display" style="top:2071px;color:var(--white)">Our Portfolio</h2>
<div class="photo tile" style="left:114px;top:2159px;width:475px;height:279px;background:linear-gradient(180deg,#4e6a2a,#6fa02c 55%,#8cc23a)" role="img" aria-label="Lawn sprinkler spraying water on green grass"></div>
<div class="photo tile" style="left:609px;top:2159px;width:477px;height:279px;background:linear-gradient(180deg,#2e3a22,#4e6a2c 60%,#6a8a38)" role="img" aria-label="Garden path with lights and a young tree at dusk"></div>
<div class="photo tile" style="left:114px;top:2457px;width:310px;height:228px;background:linear-gradient(180deg,#2a3a1e,#5a7a28 60%,#8ab43a)" role="img" aria-label="Lantern style landscape light on a lawn"></div>
<div class="photo tile" style="left:444px;top:2457px;width:312px;height:228px;background:linear-gradient(135deg,#b89a6e,#8a6c48 50%,#e08a3a)" role="img" aria-label="Trench with buried service conduit and drainage line"></div>
<div class="photo tile" style="left:774px;top:2457px;width:312px;height:228px;background:linear-gradient(180deg,#5a4a38,#5c7a30 60%,#84b03a)" role="img" aria-label="Sprinkler misting water over a garden bed"></div>

<!-- testimonials -->
<h2 class="abs section-title display" style="top:2866px"><span class="accent">What our</span> clients say</h2>

<div class="abs t-card" style="left:111px">
  <div class="t-name">Marla Quinby</div><div class="t-stars">★★★★★</div>
  <p class="t-text">Lorem ipsum dolor sit amet, consec etur adipiscing elit, sed do eiusmod tempor incididunt ut labore et do lore magna aliqua. Ut enim ad minim veniam, quis nostrud exerci tationulla labsiea.</p>
</div>
<div class="abs avatar" style="left:218px;top:2951px" role="img" aria-label="Client portrait"></div>

<div class="abs t-card" style="left:447px">
  <div class="t-name">Dorian Pell</div><div class="t-stars">★★★★★</div>
  <p class="t-text">Lorem ipsum dolor sit amet, consec etur adipiscing elit, sed do eiusmod tempor incididunt ut labore et do lore magna aliqua. Ut enim ad minim veniam, quis nostrud exerci tationulla labsiea.</p>
</div>
<div class="abs avatar" style="left:554px;top:2951px" role="img" aria-label="Client portrait"></div>

<div class="abs t-card" style="left:783px">
  <div class="t-name">Marla Quinby</div><div class="t-stars">★★★★★</div>
  <p class="t-text">Lorem ipsum dolor sit amet, consec etur adipiscing elit, sed do eiusmod tempor incididunt ut labore et do lore magna aliqua. Ut enim ad minim veniam, quis nostrud exerci tationulla labsiea.</p>
</div>
<div class="abs avatar" style="left:890px;top:2951px" role="img" aria-label="Client portrait"></div>

<div class="abs slide-btn" style="left:44px;background:var(--orange-4)"><svg width="10" height="14" viewBox="0 0 10 14"><path d="M8 2L3 7l5 5" stroke="#F0912C" stroke-width="2" fill="none"/></svg></div>
<div class="abs slide-btn" style="left:1122px;background:var(--orange)"><svg width="10" height="14" viewBox="0 0 10 14"><path d="M2 2l5 5-5 5" stroke="#fff" stroke-width="2" fill="none"/></svg></div>

<!-- footer -->
<footer class="abs footer">
  <div class="abs f-title" style="left:111px">Navigation</div>
  <ul class="abs f-nav">
    <li>Home</li><li>About Us</li><li>Irrigation Installs</li><li>Services</li><li>Landscape Lighting</li><li>Buried Wire &amp; Drainage</li><li>Contact Us</li>
  </ul>

  <div class="abs f-title" style="left:371px">Contact Us</div>
  <div class="abs f-contact" style="top:143px">
    <div class="f-icon"><svg width="14" height="18" viewBox="0 0 14 18"><path d="M7 1a6 6 0 0 0-6 6c0 4.5 6 10 6 10s6-5.5 6-10a6 6 0 0 0-6-6z" fill="#fff"/><circle cx="7" cy="7" r="2.2" fill="#F0912C"/></svg></div>
    <div><b>LOCATION:</b><span>465, Lorum Ipsum Dolore Sed,<br>United States</span></div>
  </div>
  <div class="abs f-contact" style="top:232px">
    <div class="f-icon"><svg width="16" height="16" viewBox="0 0 24 24"><path d="M6.6 10.8a15 15 0 0 0 6.6 6.6l2.2-2.2c.3-.3.7-.4 1-.2 1.1.4 2.3.6 3.6.6.6 0 1 .4 1 1V20c0 .6-.4 1-1 1A17 17 0 0 1 3 4c0-.6.4-1 1-1h3.5c.6 0 1 .4 1 1 0 1.3.2 2.5.6 3.6.1.3 0 .7-.2 1z" fill="#fff"/></svg></div>
    <div><b>PHONE:</b><span>+1 (888) 888 8888</span></div>
  </div>
  <div class="abs f-contact" style="top:303px">
    <div class="f-icon"><svg width="16" height="12" viewBox="0 0 16 12"><rect x="0" y="0" width="16" height="12" rx="1" fill="#fff"/><path d="M1 1l7 6 7-6" stroke="#F0912C" stroke-width="1.4" fill="none"/></svg></div>
    <div><b>EMAIL:</b><span>fenwickgrading@mailbox-example.net</span></div>
  </div>

  <div class="abs f-title" style="left:626px">Get In Touch</div>
  <div class="abs field" style="left:627px;top:119px;width:227px;height:47px">First Name</div>
  <div class="abs field" style="left:861px;top:119px;width:227px;height:47px">Last Name</div>
  <div class="abs field" style="left:627px;top:174px;width:227px;height:47px">Email Address</div>
  <div class="abs field" style="left:861px;top:174px;width:227px;height:47px">Phone Number</div>
  <div class="abs field" style="left:627px;top:229px;width:461px;height:84px">Message</div>
  <div class="abs btn-send">SEND MESSAGE</div>

  <div class="abs f-rule"></div>
  <div class="abs copyright">© 2024 <b>FENWICK GRADING LTD</b> &nbsp;|&nbsp; All Rights Reserved</div>
  <div class="abs social" style="left:964px;background:var(--orange)"><svg width="10" height="10"><circle cx="5" cy="5" r="4" fill="#fff"/></svg></div>
  <div class="abs social" style="left:1008px;background:var(--white)"><svg width="10" height="10"><circle cx="5" cy="5" r="4" fill="#2b2b2b"/></svg></div>
  <div class="abs social" style="left:1052px;background:var(--white)"><svg width="10" height="10"><circle cx="5" cy="5" r="4" fill="#2b2b2b"/></svg></div>
</footer>

</body>
</html>
```